Website for my photography business

I need a website for my photography business, Bram Kellet Photography. I need a website that has a landing page with a cover photo of each kind of photography I do. For example, Nature, Weddings, Portraits and Architecture. I want it so that when someone comes onto my website they have to choose which kind of photography page they want to visit. So if they click on the wedding photo it will open to a page with my wedding portfolio images and a contact me button. If they choose nature photography I want them to be redirected to an e-commerce section where they can purchase prints. Architecture and Portraits should open up to their respective portfolios with about me and contact info. I like this kind of format because I want people who come to my website for a specific type of photography to be able to be directed there easily without having to look at a mix of other kinds of photography. I will provide a few files to use as placeholders. I have already purchased the bramkelletphotography.example domain name. A Wix website would be great because I am most familiar with it but I am open to anything.

Industry/Entity Type

Photographer

Number of Pages Required

5+ page

Requirements
Must have
• Landing Page and e-commerce

```html
<!DOCTYPE html>
<html lang="en">
<head>
<meta charset="utf-8">
<title>Bram Kellet Photography</title>
<link href="https://fonts.googleapis.com/css2?family=Lato:wght@300;400;700;900&family=Raleway:wght@300;400;500&display=swap" rel="stylesheet">
<style>
:root{
  --accent:#f5a54a;
  --ink:#2b2b2b;
  --muted:#6a6a6a;
  --ghost:#e6e6e6;
  --white:#ffffff;
  --hero-top:#2c3a3c;
  --hero-mid:#8fa3a6;
  --hero-low:#1b2324;
  --footer:#1f2a2b;
}
*{box-sizing:border-box;margin:0;padding:0}
html,body{width:1200px;height:4149px;overflow:hidden;background:var(--white)}
body{position:relative;font-family:"Lato",sans-serif;color:var(--ink)}
.abs{position:absolute}
.photo{position:absolute}

/* hero */
.hero{left:0;top:0;width:1200px;height:636px;
  background:radial-gradient(ellipse 420px 300px at 600px 300px,#c9d6d6 0%,#8fa3a6 45%,transparent 80%),
  linear-gradient(180deg,var(--hero-top) 0%,var(--hero-mid) 45%,#5d6f70 70%,var(--hero-low) 100%)}
.nav a{position:absolute;top:53px;font:700 12px "Lato",sans-serif;color:var(--ink);text-decoration:none;letter-spacing:.5px;transform:translateX(-50%)}
.brand{position:absolute;left:600px;top:50px;transform:translateX(-50%);font:400 15px "Lato",sans-serif;color:var(--ink);white-space:nowrap}
.hero-title{position:absolute;left:0;width:1200px;top:254px;text-align:center;font:400 74px "Raleway",sans-serif;color:var(--white);letter-spacing:2px}
.hero-sub{position:absolute;left:0;width:1200px;top:348px;text-align:center;font:500 22px "Raleway",sans-serif;color:var(--white);letter-spacing:1px}
.hero-btn{position:absolute;left:491px;top:406px;width:219px;height:51px;border:2px solid rgba(255,255,255,.8);color:var(--white);font:400 14px "Lato",sans-serif;display:flex;align-items:center;justify-content:center}

/* section headings */
.sec-ghost{position:absolute;left:0;width:1200px;text-align:center;font:900 56px "Lato",sans-serif;color:var(--ghost);letter-spacing:6px}
.sec-title{position:absolute;left:0;width:1200px;text-align:center;font:700 28px "Lato",sans-serif;color:var(--ink);letter-spacing:1px}

/* category panels */
.card{position:absolute;border:2px solid var(--accent)}
.panel{position:absolute;background:var(--white)}
.cat-title{font:400 24px "Lato",sans-serif;color:var(--ink);letter-spacing:1px;margin-bottom:12px}
.cat-text{font:400 11.5px/18px "Lato",sans-serif;color:var(--muted)}
.cat-text p+p{margin-top:17px}
.btn{display:inline-flex;align-items:center;justify-content:center;width:119px;height:34px;border:2px solid var(--ink);font:700 10px "Lato",sans-serif;letter-spacing:.5px;color:var(--ink)}

/* about */
.about-text{position:absolute;left:150px;top:2566px;width:400px;font:400 11.5px/18px "Lato",sans-serif;color:var(--muted)}
.about-text p+p{margin-top:18px}
.line{position:absolute;border:2px solid var(--accent)}

/* reviews */
.review-text{position:absolute;left:654px;top:3152px;width:370px;font:400 11.5px/18px "Lato",sans-serif;color:var(--ink)}
.review-text p+p{margin-top:18px}
.review-author{font:700 13px "Lato",sans-serif;margin-top:22px}

/* contact */
.contact{left:0;top:3523px;width:1200px;height:600px;
  background:linear-gradient(180deg,#a87737 0%,#b98a4a 35%,#9c7a4c 58%,#3f6f6a 75%,#134e52 100%)}
.contact-title{position:absolute;left:644px;top:3574px;width:200px;text-align:center;font:400 26px "Lato",sans-serif;color:var(--white);letter-spacing:1px}
.info{position:absolute;left:168px;display:flex;align-items:center;gap:22px;font:400 13px "Lato",sans-serif;color:var(--white)}
.info svg{width:38px;height:38px}
.field{position:absolute;border:2px solid rgba(255,255,255,.9);color:var(--white);font:400 13px "Lato",sans-serif;padding:14px 20px}
.send{position:absolute;left:625px;top:3924px;width:222px;height:56px;border:2px solid rgba(255,255,255,.9);color:var(--white);font:400 14px "Lato",sans-serif;display:flex;align-items:center;justify-content:center}
.social{position:absolute;top:4023px;width:44px;height:44px;border-radius:50%;background:var(--white);color:var(--ink);font:700 9px "Lato",sans-serif;display:flex;align-items:center;justify-content:center}
.footer{position:absolute;left:0;top:4123px;width:1200px;height:26px;background:var(--footer);color:var(--white);font:400 12px "Lato",sans-serif;text-align:center;line-height:26px}
</style>
</head>
<body>

<!-- Hero -->
<header class="abs hero" role="img" aria-label="Cave opening with misty waterfall and a silhouetted figure standing on rocks"></header>
<nav class="nav">
  <a style="left:320px">PORTFOLIO</a>
  <a style="left:430px">ABOUT</a>
  <span class="brand">Bram Kellet Photography</span>
  <a style="left:796px">REVIEWS</a>
  <a style="left:904px">CONTACT</a>
</nav>
<h1 class="hero-title">BRAM KELLET</h1>
<div class="hero-sub">PHOTOGRAPHER</div>
<div class="hero-btn">CONTACT NOW</div>

<!-- Portfolio -->
<div class="sec-ghost" style="top:668px">PORTFOLIO</div>
<h2 class="sec-title" style="top:694px">PORTFOLIO</h2>

<!-- Nature -->
<div class="card" style="left:599px;top:747px;width:449px;height:201px"></div>
<div class="photo" style="left:150px;top:744px;width:449px;height:450px;background:linear-gradient(160deg,#2f4a2e 0%,#50633f 35%,#c9783a 55%,#e9eef2 75%,#ffffff 100%)" role="img" aria-label="Red fox sitting on snow among pine branches"></div>
<div class="abs" style="left:617px;top:756px;width:400px">
  <div class="cat-title">NATURE</div>
  <div class="cat-text">Nature photography covers shooting flora and fauna. This means plants, flowers, and animals, photographed in their immediate environments.<br>It's challenging because of the variety of subjects and</div>
</div>
<div class="abs" style="left:617px;top:891px"><span class="btn">VIEW MORE</span></div>
<div class="photo" style="left:599px;top:970px;width:449px;height:224px;background:radial-gradient(ellipse 80px 60px at 52% 50%,#7a4a2a 0%,#2c4a2a 60%,#16291a 100%)" role="img" aria-label="Fox peering through dark green foliage"></div>

<!-- Marriage -->
<div class="card" style="left:740px;top:1202px;width:293px;height:228px"></div>
<div class="photo" style="left:150px;top:1202px;width:299px;height:238px;background:linear-gradient(135deg,#8a7a70 0%,#b7a89c 50%,#6d5f58 100%)" role="img" aria-label="Dark wedding ring resting on a stone"></div>
<div class="photo" style="left:451px;top:1202px;width:298px;height:238px;background:linear-gradient(160deg,#b48a4a 0%,#e6cf9a 40%,#6a4a3a 75%,#2e2e3e 100%)" role="img" aria-label="Wedding couple embracing under hanging lights"></div>
<div class="abs" style="left:763px;top:1210px;width:255px">
  <div class="cat-title">MARRIAGE</div>
  <div class="cat-text">Wedding photography is a specialty in photography that is primarily focused on the photography of events and activities relating to weddings. It may include other types of portrait photography of the couple before the official wedding day, such as a</div>
</div>
<div class="abs" style="left:763px;top:1379px"><span class="btn">VIEW MORE</span></div>

<!-- Portraits -->
<div class="card" style="left:118px;top:1656px;width:482px;height:202px"></div>
<div class="photo" style="left:148px;top:1450px;width:450px;height:224px;background:linear-gradient(90deg,#d8d8d8 0%,#9a9a9a 45%,#3a3a3a 70%,#cfcfcf 100%)" role="img" aria-label="Black and white portrait of a woman"></div>
<div class="panel" style="left:148px;top:1674px;width:450px;height:182px"></div>
<div class="photo" style="left:598px;top:1450px;width:449px;height:448px;background:linear-gradient(135deg,#e8e8e8 0%,#a8a8a8 40%,#6c6c6c 65%,#d4d4d4 100%)" role="img" aria-label="Black and white close-up of crossed arms and knees"></div>
<div class="abs" style="left:176px;top:1678px;width:385px">
  <div class="cat-title">POTRAITS</div>
  <div class="cat-text">Portrait photography is the art of capturing the inherent character of your subject within a photograph. While that quizzical definition covers the basics, portrait photography goes way beyond just clicking pictures of people.</div>
</div>
<div class="abs" style="left:176px;top:1811px"><span class="btn">VIEW MORE</span></div>

<!-- Architecture -->
<div class="card" style="left:709px;top:1917px;width:340px;height:531px"></div>
<div class="panel" style="left:733px;top:1919px;width:314px;height:410px"></div>
<div class="photo" style="left:150px;top:1909px;width:291px;height:222px;background:linear-gradient(180deg,#9fc7c9 0%,#e9ece8 45%,#c9b9a0 100%)" role="img" aria-label="Museum courtyard with glass roof and white rotunda"></div>
<div class="photo" style="left:443px;top:1909px;width:290px;height:222px;background:linear-gradient(150deg,#f2f2f2 0%,#d9dadb 45%,#2a2c30 70%,#c8c8c8 100%)" role="img" aria-label="Curving white modern building facade"></div>
<div class="photo" style="left:150px;top:2133px;width:583px;height:298px;background:linear-gradient(180deg,#d7e0e6 0%,#b07a5a 35%,#8d5e44 70%,#6a7a4e 100%)" role="img" aria-label="Brick and glass campus building"></div>
<div class="abs" style="left:746px;top:1919px;width:250px">
  <div class="cat-title">ARCHITECTURE</div>
  <div class="cat-text">
    <p>Architecture photography (also referred to as building photography or structure photography) generally means photography that focuses on buildings.</p>
    <p>&nbsp;It can include shooting building exteriors and interiors, as well as bridges, other structures, and cityscapes.</p>
    <p>The medium has remained popular for all these years, and that's no surprise when you consider the significance of architecture.</p>
    <p>Buildings do much more than provide us with shelter. They are also works of art and long-lasting cultural symbols.</p>
  </div>
</div>
<div class="abs" style="left:746px;top:2287px"><span class="btn">VIEW MORE</span></div>

<!-- About -->
<div class="sec-ghost" style="top:2465px">ABOUT</div>
<h2 class="sec-title" style="top:2491px">ABOUT</h2>
<div class="about-text">
  <p>Photography and people are my great passions, in life. As a natural storyteller, I am drawn to and driven by the challenge of constructing cohesive visual narratives.</p>
  <p>Whether I'm creating a designer's lookbook, executing a national, advertising campaign, developing an evocative editorial, or crafting a Vellum Monthly inspired portrait for an individual, it is a privilege and honor to collaborate with, and create alongside, my diverse, amazing, brilliant, beautiful, talented clients and colleagues.</p>
  <p>As an educator and mentor, I strive to embolden individuals in the photo-sphere, with the knowledge, skills, and self-assuredness to realize their own respective creative projects and artistic</p>
  <p>In all that I do and create, I aspire to empower expression and impel indivduality.</p>
</div>
<div class="abs" style="left:150px;top:2874px;width:188px;height:42px;border:2px solid var(--ink);font:700 12px 'Lato',sans-serif;display:flex;align-items:center;justify-content:center">CONTACT NOW</div>
<div class="line" style="left:825px;top:2624px;width:334px;height:330px"></div>
<div class="line" style="left:501px;top:2771px;width:60px;height:140px;border-right:none"></div>
<div class="photo" style="left:564px;top:2544px;width:557px;height:368px;background:linear-gradient(180deg,#e4e8ec 0%,#cfd3d6 40%,#9c8f7c 62%,#b0603a 85%,#8a4a2e 100%)" role="img" aria-label="Photographer with camera on red canyon rocks"></div>
<div class="photo" style="left:514px;top:2779px;width:270px;height:175px;background:linear-gradient(180deg,#e6e6e6 0%,#8a8a8a 45%,#2e2e2e 75%,#1a1a1a 100%)" role="img" aria-label="Camera on tripod above a misty lake"></div>

<!-- Reviews -->
<div class="sec-ghost" style="top:2994px">REVIEWS</div>
<h2 class="sec-title" style="top:3014px">REVIEWS</h2>
<div class="line" style="left:314px;top:3065px;width:334px;height:300px;border-bottom:none"></div>
<div class="line" style="left:361px;top:3146px;width:693px;height:329px"></div>
<div class="panel" style="left:609px;top:3148px;width:442px;height:300px"></div>
<div class="photo" style="left:95px;top:3081px;width:514px;height:363px;background:radial-gradient(ellipse 180px 130px at 50% 55%,#2a2a2a 0%,#6c6f72 45%,#d9dde0 75%,#eef0f2 100%)" role="img" aria-label="Hand holding a black mirrorless camera"></div>
<div class="review-text">
  <p>I have always hated having my picture taken — I always felt so "posed" and "insincere". It was a very relaxed experience, and he captures you in your true element. I got to see a few of the shots he had taken, and I really cannot wait for the end results!! Thank you, Rowan!!"</p>
  <p>"Such a cool experience with this guy! let's you choose the style and vibe and a very comfortable studio to be in! will be back soon!"</p>
  <p>"I have an online pet boutique and needed some updated product photography. Rowan Hale did an amazing job. I got the images quickly and his pricing is very reasonable."</p>
  <div class="review-author">-MIRA SOLE</div>
</div>

<!-- Contact -->
<section class="abs contact" role="img" aria-label="Aerial view of sandy beach meeting turquoise sea"></section>
<h2 class="contact-title">LETS WORK?</h2>
<div class="info" style="top:3647px">
  <svg viewBox="0 0 24 24"><path fill="#fff" d="M12 2a7 7 0 0 0-7 7c0 5 7 13 7 13s7-8 7-13a7 7 0 0 0-7-7zm0 9.5A2.5 2.5 0 1 1 12 6.5a2.5 2.5 0 0 1 0 5z"/></svg>
  <span>New York, USA</span>
</div>
<div class="info" style="top:3802px">
  <svg viewBox="0 0 24 24"><path fill="#fff" d="M6.6 10.8a15 15 0 0 0 6.6 6.6l2.2-2.2a1 1 0 0 1 1-.25 11.4 11.4 0 0 0 3.6.57 1 1 0 0 1 1 1V20a1 1 0 0 1-1 1A17 17 0 0 1 3 4a1 1 0 0 1 1-1h3.5a1 1 0 0 1 1 1c0 1.25.2 2.45.57 3.6a1 1 0 0 1-.25 1z"/></svg>
  <span>+ 1 555 014 2320</span>
</div>
<div class="info" style="top:3952px">
  <svg viewBox="0 0 24 24"><path fill="none" stroke="#fff" stroke-width="1.6" d="M3 6h18v12H3zM3 6l9 7 9-7M3 18l7-6M21 18l-7-6"/></svg>
  <span>hello@bramkellet.example</span>
</div>
<div class="field" style="left:480px;top:3658px;width:259px;height:65px">Name</div>
<div class="field" style="left:770px;top:3658px;width:252px;height:65px">Email ID</div>
<div class="field" style="left:480px;top:3748px;width:543px;height:147px">Message</div>
<div class="send">Send Message</div>
<div class="social" style="left:644px">FEED</div>
<div class="social" style="left:711px">PICS</div>
<div class="social" style="left:777px">WORK</div>
<footer class="footer">Copyright 2020 @ BramKelletPhotography</footer>

</body>
</html>
```